Coastal Learner Bureau business cards

Australian company about to start offering its services. We recruit international students to come to study English, vocational education and postgraduate courses in Australia. We help them find the institution and select the right city they want to come to Australia. We are a young, online oriented and supportive agency. Our clients are between 18 and 35 years old, mainly University students, young professionals or people with work experience. We provide much more information that any other agency offer. We administrate a Facebook group with more than 11.000 members that daily ask questions about general information when coming to Australia, while they are here and even after they leave the country

Target Market(s)

International students from South America, Central America and Europe

Industry/Entity Type

Student

Contact Information for Business Card

Tomas Bilbrea
Managing Director
tomas@kelvarin.com.au
www.kelvoria.com.au
+61 491058264
Melbourne, Australia

Font styles to use
Serif
Sans Serif

Colors

Designer to choose colors to be used in the design.

Requirements
Must have
• Horizontal design
• Standard business card size and shape. If font uses green or yellow colours, they will have to match the ones from the logo
Nice to have
• UPDATE: Use the contents of the green image to design one of the card sides. Use our logo in the background of that side as watermark.
• Passport image, or immigration stamps. A picture of the Yarra River (from Melbourne) would be cool as well.
Should not have
• Non-standard business card size and shape
• Not black as the background colour of any sides as we are not a VIP agency or a hight class service. We are orientes to young people and they like colours, pictures, something attractive.
• Vertical design
• NO YELLOW or BLACK AS THE BACKGROUND COLOUR OF ANY SIDE OF THE BIZ CARD

```html
<!DOCTYPE html>
<html lang="en">
<head>
<meta charset="utf-8">
<title>Kelvoria Business Cards</title>
<link href="https://fonts.googleapis.com/css2?family=PT+Sans:ital,wght@0,400;0,700;1,700&display=swap" rel="stylesheet">
<style>
  :root {
    --page-bg: #e7e8ea;
    --brand-green: #04603d;
    --brand-green-soft: #0b6e48;
    --brand-yellow: #e4b323;
    --ink: #2b2b2b;
    --card-white: #ffffff;
  }
  * { box-sizing: border-box; margin: 0; padding: 0; }
  html, body {
    width: 1200px;
    height: 934px;
    overflow: hidden;
  }
  body {
    background: var(--page-bg);
    font-family: "PT Sans", sans-serif;
    display: flex;
    align-items: center;
    justify-content: center;
    gap: 40px;
  }
  .card {
    position: relative;
    width: 540px;
    height: 309px;
    overflow: hidden;
    box-shadow: 0 6px 18px rgba(0, 0, 0, 0.12);
  }

  /* Front side */
  .card--front {
    background: var(--brand-green);
  }
  .front__map {
    position: absolute;
    inset: 0;
    background: radial-gradient(ellipse at 50% 40%, var(--brand-green-soft) 0%, var(--brand-green) 70%);
  }
  .front__brand {
    position: absolute;
    top: 112px;
    left: 0;
    right: 0;
    text-align: center;
    color: var(--card-white);
    font-size: 46px;
    font-weight: 700;
    letter-spacing: 0.5px;
  }
  .front__tagline {
    position: absolute;
    bottom: 38px;
    left: 0;
    right: 0;
    text-align: center;
    color: var(--brand-yellow);
    font-size: 17px;
    font-weight: 700;
    font-style: italic;
    letter-spacing: 0.4px;
  }

  /* Back side */
  .card--back {
    background: var(--card-white);
  }
  .back__brand {
    position: absolute;
    top: 88px;
    left: 40px;
    color: var(--brand-green);
    font-size: 44px;
    font-weight: 700;
  }
  .contact {
    position: absolute;
    top: 68px;
    right: 36px;
    text-align: right;
    color: var(--ink);
    font-size: 13.5px;
    line-height: 1.35;
  }
  .contact__name {
    font-weight: 700;
    color: var(--brand-green);
    font-size: 14px;
  }
  .contact__surname { color: var(--brand-yellow); }
  .contact__rule {
    display: inline-block;
    width: 26px;
    height: 2px;
    background: var(--brand-green);
    margin: 8px 0 26px;
  }
  .contact__label {
    font-weight: 700;
    color: var(--brand-yellow);
  }
  .back__website {
    position: absolute;
    left: 40px;
    bottom: 34px;
    color: var(--brand-green);
    font-size: 17px;
    letter-spacing: 1.2px;
  }
</style>
</head>
<body>

  <section class="card card--front">
    <div class="front__map" role="img" aria-label="Faint world map in darker green across the card background"></div>
    <div class="front__brand">Kelvoria</div>
    <p class="front__tagline">Hacemos más por ti!</p>
  </section>

  <section class="card card--back">
    <div class="back__brand">Kelvoria</div>
    <div class="contact">
      <p class="contact__name">Tomas <span class="contact__surname">Bilbrea</span></p>
      <p class="contact__title">Managing Director</p>
      <span class="contact__rule"></span>
      <p><span class="contact__label">phone</span>: +61 491058264</p>
      <p><span class="contact__label">email</span>: tomas@kelvarin.com.au</p>
      <p><span class="contact__label">address</span>: Melbourne, Australia</p>
    </div>
    <p class="back__website">www.kelvoria.com.au</p>
  </section>

</body>
</html>
```